Fitness Equipment & Service

I want to make the card eye catching and fun. We are called Corvane Motion Limited and we are based in Wales. We sell, install and service all types of fitness equipment from Skipping ropes, right through the Dumbbells, Kettle bells and Barbells through to state of the art Treadmills, Running Machines and Strength Equipment. We also design and install changing room furniture and lockers.

TYPOGRAPHY
We would like to use Futrura. Futura has an appearance of efficiency and forwardness. The typeface is derived
from simple geometric forms (near-perfect circles, triangles and squares) and is based on strokes of
near-even weight, which are low in contrast. This is most visible in the almost perfectly round stroke of
the o, which is nonetheless slightly ovoid.
The lowercase has tall ascenders, which rise above the cap line. The uppercase
characters present proportions similar to those of classical Roman capitals.

TYPOGRAPHIC CONSIDERATIONS
No Strike though
No Horizontal Scaling
No Drop Shadows
No Effects
Never use less than 120% Leading

OUR CORPORATE COLOURS
BRAND GUIDELINES
We were thinking that our primary colour palette consists of the Acid Green (Pantone 382) and Process Black.

We work closely with tquarly Ltd and would like to include their name on the card somewhere. I have attached images of the other brands that we work with as an idea or the small icons I have included that illustrate what we do?. I have very kindly been given permission to use any of the images off the files that I have included below, so I hope these help. I will include these below. I would be open to suggestions if it made the card more striking Can you do it?
Updates

Hi All, Just wanted to add a few thoughts but you are the guys with the creative visions (thats why are here) We are based in Wales, UK and we would be open to lots of different ideas on a theme but must be eye catching, Bold and FUN. If you can or think that the Welsh or any dragon could be put in there then go for it (its not a must have) We have also added some ideas for colour but again its over to you!! GO FOR IT ! Thanks and look forward to your visions! Owen

Hi All, Just thought I would sen through the contact details that need to be on the card. (if you want to play around with icons instead of the wording twitter, Facebook, go for it): Corvane Motion Limited Owen Pritchard Managing Director Mob: +44 (0)7582 913 406 e-mail: sales@corvanemotion.co.uk Web: Corvanemotion.co.uk twitter: @motionLetterbin Facebook: Corvane Motion Limited

```html
<!DOCTYPE html>
<html lang="en">
<head>
<meta charset="utf-8">
<title>Corvane Motion Limited – Business Card</title>
<link rel="stylesheet" href="https://fonts.googleapis.com/css2?family=Jost:wght@400;500&family=Arimo:wght@400;700&display=swap">
<style>
  :root {
    --page-bg: #e9e7e3;
    --card-white: #ffffff;
    --card-grey: #d9dadc;
    --navy-deep: #14306a;
    --navy-mid: #1f4b94;
    --navy-ink: #121b48;
    --gold: #c9a14a;
    --gold-light: #f0d27c;
    --text-light: #ffffff;
  }
  * { box-sizing: border-box; margin: 0; padding: 0; }
  html, body { width: 1200px; height: 950px; overflow: hidden; }
  body {
    background: var(--page-bg);
    position: relative;
    font-family: "Arimo", Arial, sans-serif;
  }
  .card {
    position: absolute;
    left: 280px;
    width: 640px;
    height: 366px;
    overflow: hidden;
    box-shadow: 0 6px 18px rgba(0,0,0,0.18);
  }
  /* Back of card */
  .card-back {
    top: 70px;
    background: linear-gradient(160deg, var(--card-white) 0%, var(--card-white) 35%, var(--card-grey) 100%);
  }
  .back-mark {
    position: absolute;
    left: 50%;
    top: 78px;
    transform: translateX(-50%);
    display: flex;
    flex-direction: column;
    align-items: center;
    gap: 18px;
  }
  .back-mark .mark-circle {
    width: 120px;
    height: 120px;
    border-radius: 50%;
    background: var(--navy-mid);
  }
  .back-mark .brand-name {
    font-family: "Jost", "Futura", sans-serif;
    font-weight: 400;
    font-size: 20px;
    letter-spacing: 1.5px;
    line-height: 1.2;
    color: var(--navy-ink);
    text-transform: uppercase;
  }
  /* Front of card */
  .card-front {
    top: 510px;
    background: var(--card-white);
  }
  .front-shapes { position: absolute; inset: 0; }
  .front-brand {
    position: absolute;
    left: 36px;
    top: 40px;
    display: flex;
    align-items: center;
    gap: 14px;
  }
  .front-brand .mark-square {
    width: 44px;
    height: 44px;
    background: var(--navy-ink);
  }
  .front-brand .brand-name {
    font-family: "Jost", "Futura", sans-serif;
    font-weight: 500;
    font-size: 30px;
    line-height: 1.2;
    letter-spacing: 1px;
    color: var(--navy-ink);
    text-transform: uppercase;
  }
  .holder {
    position: absolute;
    left: 26px;
    top: 184px;
    color: var(--text-light);
    line-height: 1.25;
  }
  .holder .holder-name { font-weight: 700; font-size: 21px; }
  .holder .holder-role { font-size: 16px; margin-bottom: 12px; }
  .holder .holder-address { font-size: 16px; font-style: normal; }
  .contacts {
    position: absolute;
    right: 22px;
    top: 222px;
    list-style: none;
    color: var(--text-light);
    font-size: 15.5px;
    line-height: 1.25;
  }
  .contacts li {
    display: flex;
    justify-content: flex-end;
    align-items: center;
    gap: 8px;
    margin-bottom: 3px;
  }
  .contacts svg { width: 14px; height: 14px; flex: none; }
</style>
</head>
<body>

  <section class="card card-back" aria-label="Card back">
    <div class="back-mark">
      <span class="mark-circle"></span>
      <span class="brand-name">Corvane Motion Limited</span>
    </div>
  </section>

  <section class="card card-front" aria-label="Card front">
    <svg class="front-shapes" viewBox="0 0 640 366" preserveAspectRatio="none" aria-hidden="true">
      <defs>
        <linearGradient id="navyFill" x1="0" y1="0" x2="1" y2="1">
          <stop offset="0" stop-color="var(--navy-mid)"/>
          <stop offset="1" stop-color="var(--navy-deep)"/>
        </linearGradient>
        <linearGradient id="goldFill" x1="0" y1="0" x2="1" y2="0">
          <stop offset="0" stop-color="var(--gold)"/>
          <stop offset="0.6" stop-color="var(--gold-light)"/>
          <stop offset="1" stop-color="var(--gold)"/>
        </linearGradient>
      </defs>
      <polygon points="0,150 290,150 316,196 302,196 282,162 0,162" fill="url(#goldFill)"/>
      <polygon points="0,166 280,166 300,200 640,200 640,366 0,366" fill="url(#navyFill)"/>
    </svg>

    <div class="front-brand">
      <span class="mark-square"></span>
      <span class="brand-name">Corvane Motion Limited</span>
    </div>

    <div class="holder">
      <p class="holder-name">Owen Pritchard</p>
      <p class="holder-role">Managing Director</p>
      <address class="holder-address">14 Ashgrove Lane<br>Caerwen, CF31 4QX</address>
    </div>

    <ul class="contacts">
      <li>+44 (0)7582 913 406
        <svg viewBox="0 0 14 14" aria-label="Phone"><rect x="3.5" y="1" width="7" height="12" rx="1.2" fill="none" stroke="#fff" stroke-width="1.3"/><circle cx="7" cy="11" r="0.8" fill="#fff"/></svg>
      </li>
      <li>sales@corvanemotion.co.uk
        <svg viewBox="0 0 14 14" aria-label="Email"><rect x="1" y="3" width="12" height="8" fill="#fff"/><polyline points="1,3 7,8 13,3" fill="none" stroke="var(--navy-deep)" stroke-width="1.1"/></svg>
      </li>
      <li>Corvanemotion.co.uk
        <svg viewBox="0 0 14 14" aria-label="Website"><circle cx="7" cy="7" r="6" fill="#fff"/></svg>
      </li>
      <li>@motionLetterbin
        <svg viewBox="0 0 14 14" aria-label="Social handle"><rect x="1" y="1" width="12" height="12" rx="2" fill="#fff"/></svg>
      </li>
      <li>Corvane Motion Limited
        <svg viewBox="0 0 14 14" aria-label="Social page"><rect x="1" y="1" width="12" height="12" rx="2" fill="#fff"/></svg>
      </li>
    </ul>
  </section>

</body>
</html>
```